Willow Creek Gatherings Event Planning in need of a design!!

Event Planning company, does a variety of events. I like simple more rustic designs focused on almond blossoms. We are based out of Northern California, the heart of almond country. I would like to see colors in light pinks, beige, light browns, whites or creams. the final design should communicate rustic simplicity. Below are some pictures of Almond blossoms and design ideas I prefer the one called Tulip Grove. Thanks

Target Market(s)

Women in the mid twenties and older. They should be in the upper middle class in need of an amazing party design and coordinator

Industry/Entity Type

Event Planning

Contact Information for Business Card

Maren Lockwood 530-624-0295almondbaffairs@gmail.comalmondblossomaffairs.com

Font styles to use
Other font styles liked:
• Amatic SC

Requirements
Must have
• almond blossom
• my information
• simplicity
Nice to have
• rustic design
• vintage feel
• whimsical
Should not have
• i like pink but not over the top

```html
<!DOCTYPE html>
<html lang="en">
<head>
<meta charset="utf-8">
<title>Willow Creek Gatherings – Business Card</title>
<link rel="stylesheet" href="https://fonts.googleapis.com/css2?family=Source+Sans+3:wght@400;600&display=swap">
<style>
  :root {
    --stage: #eee8e1;
    --card: #fcf8f2;
    --band-top: #d4a9a2;
    --band-bottom: #a8866a;
    --brand: #8c6449;
    --name: #a66f66;
    --rule: #cfaaa1;
    --ink: #4b3b31;
    --icon: #b07d72;
    --bloom-light: rgba(250, 240, 238, 0.95);
    --bloom-mid: rgba(232, 212, 206, 0.85);
    --bloom-deep: rgba(196, 150, 140, 0.75);
  }
  * { margin: 0; padding: 0; box-sizing: border-box; }
  html, body {
    width: 1200px; height: 900px; overflow: hidden;
    background: var(--stage);
  }
  .canvas {
    width: 1200px; height: 900px;
    display: flex; align-items: center; justify-content: center;
  }
  .card {
    position: relative; width: 900px; height: 554px;
    background: var(--card);
    border-radius: 22px; overflow: hidden;
    box-shadow: 0 14px 40px rgba(90, 60, 40, 0.14);
    font-family: "Source Sans 3", "Myriad Pro", Arial, sans-serif;
  }
  .band-top {
    position: absolute; left: 0; top: 0; width: 100%; height: 32px;
    background: var(--band-top);
  }
  .band-bottom {
    position: absolute; left: 0; top: 522px; width: 100%; height: 32px;
    background: var(--band-bottom);
  }
  .blossom-photo {
    position: absolute; left: 0; top: 32px; width: 300px; height: 395px;
    background:
      radial-gradient(ellipse 90px 80px at 60px 70px, var(--bloom-deep), transparent 100%),
      radial-gradient(ellipse 170px 230px at 90px 190px, var(--bloom-mid), transparent 100%),
      radial-gradient(ellipse 240px 320px at 60px 200px, var(--bloom-light), transparent 100%);
  }
  .brand {
    position: absolute; left: 150px; top: 140px; width: 600px;
    text-align: center; color: var(--brand); font-weight: 600;
  }
  .brand-line { display: block; font-size: 40px; line-height: 48px; letter-spacing: 3px; }
  .brand-sub { display: block; font-size: 27px; line-height: 34px; letter-spacing: 11px; margin-top: 6px; padding-left: 11px; }
  .name-row {
    position: absolute; left: 0; top: 333px; width: 100%; height: 40px;
    display: flex; align-items: center; gap: 14px;
  }
  .name-row .rule { flex: 1; height: 2px; background: var(--rule); }
  .person-name { font-size: 30px; line-height: 40px; font-weight: 600; color: var(--name); white-space: nowrap; }
  .contacts {
    position: absolute; left: 0; top: 406px; width: 100%;
    list-style: none; color: var(--ink);
    font-size: 23px; line-height: 37px;
  }
  .contacts li { display: flex; justify-content: center; align-items: center; gap: 7px; }
  .contacts svg { width: 17px; height: 17px; fill: var(--icon); flex: none; }
</style>
</head>
<body>
<main class="canvas">
  <article class="card">
    <div class="band-top"></div>
    <div class="blossom-photo" role="img" aria-label="Photograph of a white almond blossom with pink stamens"></div>

    <h1 class="brand">
      <span class="brand-line">WILLOW CREEK</span>
      <span class="brand-sub">GATHERINGS</span>
    </h1>

    <div class="name-row">
      <span class="rule"></span>
      <h2 class="person-name">Maren Lockwood</h2>
      <span class="rule"></span>
    </div>

    <ul class="contacts">
      <li>
        <svg viewBox="0 0 24 24" aria-hidden="true"><path d="M6.6 10.8a15.1 15.1 0 0 0 6.6 6.6l2.2-2.2c.3-.3.7-.4 1-.2 1.1.4 2.3.6 3.6.6.6 0 1 .4 1 1V20c0 .6-.4 1-1 1A17 17 0 0 1 3 4c0-.6.4-1 1-1h3.5c.6 0 1 .4 1 1 0 1.3.2 2.5.6 3.6.1.3 0 .7-.2 1z"/></svg>
        530-817-4362
      </li>
      <li>
        <svg viewBox="0 0 24 24" aria-hidden="true"><path d="M2 5h20v14H2zm2 2v.5l8 5 8-5V7l-8 5z"/></svg>
        willowcgather@mailbox.test
      </li>
      <li>
        <svg viewBox="0 0 24 24" aria-hidden="true"><circle cx="12" cy="12" r="10"/><path d="M2 12h20M12 2c3 3 3 17 0 20M12 2c-3 3-3 17 0 20" stroke="#fcf8f2" stroke-width="1.4" fill="none"/></svg>
        www.willowcreekgatherings.test
      </li>
    </ul>

    <div class="band-bottom"></div>
  </article>
</main>
</body>
</html>
```